BLUE & ORANGE BALM TOPICAL BOX + LABELS TO MATCH

Hello ! I hope you're up to helping with my designs again. I appreciate all your help.
I have two topicals needing redesign.
Box + Label , once the box is together, we can slap the labels together easy.
I have CBD version and THC version of both these balms, so well start w THC, then lay out the CBD. It should be eaay with few minor differences.
PLEASE USE only tHE SMALL BOX TEMPLATE,
Anyway, once the boxes are complete, I need to revise the label to match the boxes.
1.
ORANGE BALM :
(this box color I would like orange, like a jack-o-lantern (i uploaded our current label so you can match it)
KORVEN logo outlined in Gold (on LID)
(I uploaded a picture of what the oulined logo looks like)
THC SYMBOL
ORANGE BALM (GOLD) (on Front)
HIGHLY NUTRITIOUS POWERFUL THC RELIEF
net wt. 2 oz (56 g)
SIDE PANEL :
ORGANIC INGREDIENTS : Butyrospermum Parkii Butter (Shea Butter), Persia Gratissima (Avocado) Oil, Simmondsia chinesis (Gold Jojoba) Oil , Vitus Vinifera (Grape) Seed Oil, Arnica montana (Arnica) and Symphytum officinalis (Comfrey Leaf) macerated in Sunflower Oil, Calophyllum inophyllum (Tamanu) Oil, Nigella sativa (Black Seed) Oil, Locally Harvested Beeswax, THC CANNABIS EXTRACT, Pure Cannabigerol (CBG), Proprietary Blend of Therapeutic Essential Oils (including but not limited to : Yarrow , Celery Seed , Tea Tree , Lavender , Helichrysum, Pine Scotch, Rosemary, Geranium), Tocopherol (Vitamin E, antioxidant )
Color is a Natural Result of Chamomile Steam-Distillation and May Vary in Intensity. Consistency can also Vary. For Optimal Preservation, Keep in a Cool, Dark Place. Fatty Acids may Naturally Aggregate when Exposed to Temperature Extremes Forming Beads. To Fix This, Use a Hair Dryer to Melt them Back to a Smooth Consistency.
BACK PANEL :
WARNING: THIS PRODUCT IS FOR USE BY INDIVIDUALS 21 YEARS OF AGE OR OLDER OR BY REGISTERED QUALIFYING PATIENTS ONLY. IT IS ILLEGAL TO DRIVE A MOTOR VEHICLE WHILE UNDER THE INFLUENCE OF MARIJUANA.
(Outlined Box )::
WARNING: USE BY PREGNANT OR BREASTFEEDING WOMEN OR BY WOMEN PLANNING TO BECOME PREGNANT, MAY RESULT IN FETAL INJURY, PRETERM BIRTH, LOW BIRTHWEIGHT, OR DEVELOPMENTAL PROBLEMS FOR THE CHILD.
KEEP OUT OF REACH OF CHILDREN.
CENTRAL TOXIN RESPONSE BUREAU 1 800 555 0147
THE ACTUAL VALUE OF CANNABINOIDS MAY VARY FROM THE REPORTED VALUE BY +/- 10%
ACTIVATION TIME : 10 - 60 MINUTES
MADE IN A MARIJUANA FACILITY
PACKAGED BY
MIRABEL’S LUSH Co.
QX-R-748315
www.LUSHTARTS.info
2.
BLUE BALM
white box
KORVEN Gold out line, red w blue leaf
FRONT PANEL :
BLUE BALM (blue)
net wt. 2 oz (56 g)
Ingredients : Butyrospermum Parkii Butter (Shea Butter), Aloe Barbadensis (Aloe Vera) Leaf Extract, Coco Nucifera (Coconut) Oil, THC CANNABIS EXTRACT, Cannabis Sativa Seed Oil, Pure Cannabidol (Hemp Extract), Prunes Armeniaca (Apricot) Kernal Oil, Hydrogenated Vegetable (Soybean) Oil, Prunus Amygdalus Dulcis (Sweet Almond Oil), Vitus Vinifera (Grape) Seed Oil, Macadamia Ternifolia Seed Oil, Daucus Carota (Carrot) Seed Oil, Proprietary Blend of Therapeutic Essential Oils (including but not limited to : Lavender, Chamomile), Tocopherol (Vitamin E, antioxidant)

```html
<!DOCTYPE html>
<html lang="en">
<head>
<meta charset="utf-8">
<title>Korven Orange Balm – Box Panels</title>
<link rel="stylesheet" href="https://fonts.googleapis.com/css2?family=Oswald:wght@600;700&family=Roboto+Condensed:ital,wght@0,400;1,400;1,700&display=swap">
<style>
  :root{
    --page:#f2f2f2;
    --orange:#f26f22;
    --orange-light:#f5894a;
    --orange-deep:#e05f1a;
    --gold:#ffd23f;
    --red:#ee3340;
  }
  *{box-sizing:border-box;margin:0;padding:0}
  html,body{width:1200px;height:1200px;overflow:hidden;background:var(--page)}
  .sheet{position:relative;width:1200px;height:1200px}
  .panel{
    position:absolute;
    background:linear-gradient(160deg,var(--orange-light),var(--orange) 45%,var(--orange-deep));
    color:var(--gold);
  }
  .panel--lid{left:330px;top:30px;width:540px;height:540px;
    display:flex;flex-direction:column;align-items:center;justify-content:center;gap:26px}
  .panel--side{left:40px;top:600px;width:550px;height:570px;padding:34px 30px;
    font-family:"Roboto Condensed",sans-serif}
  .panel--back{left:610px;top:600px;width:550px;height:570px;padding:30px 30px;
    font-family:"Roboto Condensed",sans-serif;font-style:italic;font-weight:700;text-transform:uppercase}

  .brand{display:flex;align-items:center;gap:18px}
  .brand__name{font-family:"Oswald",sans-serif;font-weight:700;font-size:104px;
    letter-spacing:2px;color:var(--red);line-height:1}
  .brand__dot{width:44px;height:44px;border-radius:50%;background:var(--red)}
  .product-name{font-family:"Oswald",sans-serif;font-weight:700;font-size:86px;
    color:var(--gold);line-height:1;letter-spacing:1px}

  .ingredients{font-size:19px;line-height:1.28;text-align:justify;margin-bottom:22px}
  .care{font-size:16px;line-height:1.32}

  .claims{font-size:21px;line-height:1.2;margin-bottom:14px}
  .notice{font-size:15px;line-height:1.3;margin-bottom:10px}
  .notice--center{text-align:center}
  .warning-box{border:2px solid var(--gold);padding:12px 14px;font-size:15px;line-height:1.3;
    text-align:center;margin-top:8px}
  .warning-box p+p{margin-top:10px}
  .disclaimer{margin-top:12px;font-size:12.5px;font-weight:400;text-transform:none;line-height:1.3;text-align:center}
</style>
</head>
<body>
<main class="sheet">

  <section class="panel panel--lid">
    <div class="brand">
      <span class="brand__name">KORVEN</span>
      <span class="brand__dot"></span>
    </div>
    <h1 class="product-name">ORANGE BALM</h1>
  </section>

  <section class="panel panel--side">
    <p class="ingredients">ORGANIC INGREDIENTS : Butyrospermum Parkii Butter (Shea Butter), Persia Gratissima (Avocado) Oil, Simmondsia chinesis (Gold Jojoba) Oil, Vitus Vinifera (Grape) Seed Oil, Arnica montana (Arnica) and Symphytum officinalis (Comfrey Leaf) macerated in Sunflower Oil, Calophyllum inophyllum (Tamanu) Oil, Nigella sativa (Black Seed) Oil, Locally Harvested Beeswax, THC CANNABIS EXTRACT, Pure Cannabigerol (CBG), Proprietary Blend of Therapeutic Essential Oils (including but not limited to : Yarrow, Celery Seed, Tea Tree, Lavender, Helichrysum, Pine Scotch, Rosemary, Geranium), Tocopherol (Vitamin E, antioxidant )</p>
    <p class="care">Color is a Natural result of the Phytonutrients within the Formula and May Vary in Intensity. Consistency may also Vary. For Optimal Preservation, Keep in a Cool, Dark Place. Fatty Acids may Naturally Aggregate when Exposed to Temperature Extremes Forming Beads. To Fix This, Use a Hair Dryer to Melt them Back to a Smooth Consistency. For Best Results, Apply to Skin after a warm wash. Botanical oils and Healing compounds are better able to lock into the dermis when the pores are clean, warm and open.</p>
  </section>

  <section class="panel panel--back">
    <p class="claims">Potent Relief • Ultra Healing Non Psychoactive • Small Batch Plant Based • High THC Formula</p>
    <p class="notice">Activation Time : This product is for use by individuals 21 years of age or older or by registered qualifying patients only. It is illegal to drive a motor vehicle while under the influence of marijuana. Activation time : 30 minutes.</p>
    <p class="notice notice--center">Keep out of reach of children.<br>Central Toxin Response Bureau 1 800 555 0147</p>
    <div class="warning-box">
      <p>Warning: Use by pregnant or breastfeeding women or by women planning to become pregnant, may result in fetal injury, preterm birth, low birthweight, or developmental problems for the child.</p>
      <p>The actual value of cannabinoids may vary from the reported value by +/-10%<br>Made in a marijuana facility<br>Packaged by : Mirabel’s Lush QX-R-748315</p>
    </div>
    <p class="disclaimer">These Statements have not been evaluated by the FDA. This product is not intended to diagnose, treat, cure, or prevent any disease or condition.</p>
  </section>

</main>
</body>
</html>
```